Visitenkarten-Design für IT-Service
Zielgruppe
IT-Service
Zielgruppe sind mittelständische Unternehmen aus unterschiedlichen Branchen, die eine Betreuung ihre IT benötigen.
Die Visitenkarte darf sich gerne vom Standard abheben, ein 'Eyecatcher' wär schön
Aufgabenstellung
Es sollen auf der einen Seite das Logo und der Name und auf der anderen die notwendigen Information:
Firmenname: Kolvane GmbH und Logo
Berliner IT-Service
Personenname: Vorname Nachname
Funktion, zB: Geschäftsführer
Web: www.kolvane.de
Schriftart im Logo ist Expansiva https://www.glyphmarkt.example/de/expansiva.font

```html
<!DOCTYPE html>
<html lang="de">
<head>
<meta charset="utf-8">
<title>Kolvane GmbH – Visitenkarten</title>
<link rel="stylesheet" href="https://fonts.googleapis.com/css2?family=Michroma&family=Open+Sans:wght@300;400;600&display=swap">
<style>
  :root {
    --page: #ffffff;
    --ink-dark: #1b1b1b;
    --navy: #22406b;
    --band-2: #1f5680;
    --band-3: #1c6a93;
    --band-4: #1a7aa4;
    --band-5: #1888ae;
    --teal: #1a87b0;
    --white: #ffffff;
    --edge: #c9c9c9;
  }
  * { margin: 0; padding: 0; box-sizing: border-box; }
  html, body { width: 741px; height: 1200px; overflow: hidden; background: var(--page); }
  body { position: relative; font-family: "Open Sans", sans-serif; }

  .card {
    position: absolute; width: 270px; height: 465px;
    border-radius: 24px; overflow: hidden;
    display: flex; flex-direction: column;
  }
  .card--dark { background: var(--ink-dark); }
  .card--light { background: var(--white); border: 1px solid var(--edge); }
  .front-dark { left: 77px; top: 53px; }
  .back-dark { left: 388px; top: 53px; }
  .front-light { left: 81px; top: 580px; }
  .back-light { left: 392px; top: 580px; }

  /* Front */
  .brand { position: absolute; left: 26px; top: 108px; display: flex; align-items: center; gap: 14px; }
  .brand-mark { width: 30px; height: 30px; border-radius: 6px; background: var(--navy); }
  .brand-name { font-family: "Open Sans", sans-serif; font-weight: 600; font-size: 32px; color: var(--teal); letter-spacing: 1px; }
  .front-tag { position: absolute; left: 0; right: 0; top: 376px; text-align: center; color: var(--navy); }
  .card--light .front-tag { color: var(--navy); }
  .front-tag .company { font-weight: 600; font-size: 19px; line-height: 22px; }
  .front-tag .service { font-weight: 300; font-size: 15px; line-height: 18px; }

  /* Back */
  .back-head { height: 155px; position: relative; flex: none; }
  .back-head .symbol { position: absolute; left: 22px; top: 26px; width: 52px; height: 52px; border-radius: 10px; background: var(--navy); }
  .back-head .head-text { position: absolute; right: 22px; top: 46px; text-align: right; color: var(--teal); }
  .head-text .company { font-weight: 600; font-size: 15px; line-height: 17px; }
  .head-text .service { font-weight: 300; font-size: 13px; line-height: 16px; }

  .person { height: 55px; background: var(--navy); text-align: right; padding: 10px 18px 0 0; flex: none; }
  .person .name { font-family: "Michroma", sans-serif; font-size: 17px; line-height: 20px; letter-spacing: 1px; }
  .person .role { font-size: 13px; line-height: 16px; text-align: center; padding-left: 20px; }

  .contact-row { height: 55px; display: flex; align-items: center; padding-left: 22px; gap: 16px; font-size: 13px; flex: none; }
  .contact-row svg { width: 20px; height: 20px; flex: none; }
  .row-1 { background: var(--band-2); }
  .row-2 { background: var(--band-3); }
  .row-3 { background: var(--band-4); }
  .row-4 { background: var(--band-5); }

  .card--dark .person, .card--dark .contact-row { color: var(--ink-dark); fill: var(--ink-dark); }
  .card--light .person, .card--light .contact-row { color: var(--white); fill: var(--white); }

  .web { flex: 1; display: flex; align-items: center; justify-content: center; color: var(--teal); font-size: 13px; }
</style>
</head>
<body>

<section class="card card--dark front-dark">
  <div class="brand"><span class="brand-mark"></span><span class="brand-name">Kolvane</span></div>
  <div class="front-tag"><p class="company">Kolvane GmbH</p><p class="service">Velten Berliner IT-Service</p></div>
</section>

<section class="card card--dark back-dark">
  <header class="back-head">
    <span class="symbol"></span>
    <div class="head-text"><p class="company">Kolvane GmbH</p><p class="service">Velten Berliner IT-Service</p></div>
  </header>
  <div class="person"><p class="name">Jonas Velten</p><p class="role">Geschäftsführer</p></div>
  <div class="contact-row row-1"><svg viewBox="0 0 20 20"><path d="M10 1a6.5 6.5 0 0 0-6.5 6.5C3.5 12 10 19 10 19s6.5-7 6.5-11.5A6.5 6.5 0 0 0 10 1zm0 9a2.5 2.5 0 1 1 0-5 2.5 2.5 0 0 1 0 5z"/></svg>Lindenhofstr. 4-12 | 10117 Berlin</div>
  <div class="contact-row row-2"><svg viewBox="0 0 20 20"><path d="M4 1l3 1 1.5 4-2 1.5a11 11 0 0 0 6 6l1.5-2 4 1.5 1 3-2 2C9 19 1 11 2 3z"/></svg>030-555 41 278</div>
  <div class="contact-row row-3"><svg viewBox="0 0 20 20"><path d="M5 1h10v5H5zM2 7h16a1 1 0 0 1 1 1v7h-3v-3H4v3H1V8a1 1 0 0 1 1-1zm3 6h10v6H5z"/></svg>030-555 41 279</div>
  <div class="contact-row row-4"><svg viewBox="0 0 20 20"><path d="M1 4h18v12H1zm1.5 1.5v.3L10 11l7.5-5.2v-.3zM2.5 7.7v6.8h15V7.7L10 13z"/></svg>name@kolvane.de</div>
  <footer class="web">www.kolvane.de</footer>
</section>

<section class="card card--light front-light">
  <div class="brand"><span class="brand-mark"></span><span class="brand-name">Kolvane</span></div>
  <div class="front-tag"><p class="company">Kolvane GmbH</p><p class="service">Velten Berliner IT-Service</p></div>
</section>

<section class="card card--light back-light">
  <header class="back-head">
    <span class="symbol"></span>
    <div class="head-text"><p class="company">Kolvane GmbH</p><p class="service">Velten Berliner IT-Service</p></div>
  </header>
  <div class="person"><p class="name">Jonas Velten</p><p class="role">Geschäftsführer</p></div>
  <div class="contact-row row-1"><svg viewBox="0 0 20 20"><path d="M10 1a6.5 6.5 0 0 0-6.5 6.5C3.5 12 10 19 10 19s6.5-7 6.5-11.5A6.5 6.5 0 0 0 10 1zm0 9a2.5 2.5 0 1 1 0-5 2.5 2.5 0 0 1 0 5z"/></svg>Lindenhofstr. 4-12 | 10117 Berlin</div>
  <div class="contact-row row-2"><svg viewBox="0 0 20 20"><path d="M4 1l3 1 1.5 4-2 1.5a11 11 0 0 0 6 6l1.5-2 4 1.5 1 3-2 2C9 19 1 11 2 3z"/></svg>030-555 41 278</div>
  <div class="contact-row row-3"><svg viewBox="0 0 20 20"><path d="M5 1h10v5H5zM2 7h16a1 1 0 0 1 1 1v7h-3v-3H4v3H1V8a1 1 0 0 1 1-1zm3 6h10v6H5z"/></svg>030-555 41 279</div>
  <div class="contact-row row-4"><svg viewBox="0 0 20 20"><path d="M1 4h18v12H1zm1.5 1.5v.3L10 11l7.5-5.2v-.3zM2.5 7.7v6.8h15V7.7L10 13z"/></svg>name@kolvane.de</div>
  <footer class="web">www.kolvane.de</footer>
</section>

</body>
</html>
```